Web Developer Needs a Business Card Design

I need a personal business card design that represents me as a web developer for potential employers. I would like the background to be a dark color on the front for contrast with my logo and name. The back will have all my information along with a smaller version of the logo. I want something with a modern look and feel, not too conservative. This will be used for potential employers and freelance work.

Industry/Entity Type

Business

Contact Information for Business Card

Front should have my logo and name. The back should have all my personal information which would include: name: Tom Varulek, phone: 570-614-3098, email: tomvarulek@quillbox.net, website url: www.tomvarulek.net, logo, web developer.

Font styles to use
Sans Serif

Requirements
Must have
• Must include my logo. The color palette base color will be the logo color.

```html
<!DOCTYPE html>
<html lang="en">
<head>
<meta charset="utf-8">
<title>Tom Varulek – Business Card</title>
<link rel="stylesheet" href="https://fonts.googleapis.com/css2?family=Open+Sans:wght@400;600&display=swap">
<style>
  :root {
    --teal: #6cc3ad;
    --ink: #0b0b0b;
    --paper: #f4f4f4;
    --backdrop: #dcdcdc;
    --white: #ffffff;
  }
  html, body {
    margin: 0;
    padding: 0;
    width: 1189px;
    height: 1200px;
    overflow: hidden;
    background: var(--backdrop);
    font-family: "Open Sans", sans-serif;
  }
  .card {
    position: absolute;
    left: 140px;
    width: 917px;
    height: 522px;
    display: block;
  }
  .card--front { top: 45px; }
  .card--back { top: 623px; }
  .card-paper { fill: var(--paper); }
  .card-dark { fill: var(--ink); }
  .card-band { fill: var(--teal); }
  .mark-ring { fill: none; stroke: var(--teal); }
  .mark-name { fill: var(--teal); font-weight: 600; font-family: "Open Sans", sans-serif; }
  .holder-name { fill: var(--white); font-weight: 400; font-size: 46px; font-family: "Open Sans", sans-serif; }
  .holder-role { fill: var(--white); font-size: 29px; font-family: "Open Sans", sans-serif; }
  .divider { stroke: var(--white); stroke-width: 3; }
  .contact-text { fill: var(--white); font-size: 31px; font-family: "Open Sans", sans-serif; }
  .contact-icon-box { fill: var(--white); }
  .contact-icon-glyph { fill: none; stroke: var(--ink); stroke-width: 2; }
  .back-name { fill: var(--ink); font-weight: 600; font-size: 56px; font-family: "Open Sans", sans-serif; }
</style>
</head>
<body>

<svg class="card card--front" viewBox="0 0 1123 640" aria-label="Business card, contact side">
  <rect class="card-paper" x="0" y="0" width="1123" height="640"/>
  <path class="card-dark" d="M0 225 Q561.5 545 1123 225 L1123 610 L0 610 Z"/>
  <rect class="card-band" x="0" y="610" width="1123" height="30"/>

  <g class="brand-mark">
    <circle class="mark-ring" cx="556" cy="195" r="150" stroke-width="12"/>
    <text class="mark-name" x="556" y="209" font-size="40" text-anchor="middle">Tom Varulek</text>
  </g>

  <text class="holder-name" x="233" y="487">Tom Varulek</text>
  <text class="holder-role" x="237" y="522">web developer</text>

  <line class="divider" x1="555" y1="415" x2="555" y2="570"/>

  <g class="contact-list">
    <rect class="contact-icon-box" x="588" y="452" width="20" height="20" rx="2"/>
    <path class="contact-icon-glyph" d="M593 456 q-2 6 4 12 q6 5 8 2 l-3 -3 -2 2 q-4 -2 -5 -6 l2 -1 z"/>
    <text class="contact-text" x="621" y="473">570-614-3098</text>

    <rect class="contact-icon-box" x="588" y="490" width="20" height="16" rx="2"/>
    <path class="contact-icon-glyph" d="M590 492 L598 499 L606 492"/>
    <text class="contact-text" x="621" y="510">tomvarulek@quillbox.net</text>

    <rect class="contact-icon-box" x="588" y="525" width="20" height="20" rx="3"/>
    <circle class="contact-icon-glyph" cx="598" cy="535" r="6"/>
    <text class="contact-text" x="621" y="546">www.tomvarulek.net</text>
  </g>
</svg>

<svg class="card card--back" viewBox="0 0 1123 640" aria-label="Business card, logo side">
  <rect class="card-paper" x="0" y="0" width="1123" height="640"/>
  <g class="brand-mark">
    <circle class="mark-ring" cx="552" cy="259" r="166" stroke-width="13"/>
    <text class="mark-name" x="552" y="274" font-size="44" text-anchor="middle">Tom Varulek</text>
  </g>
  <text class="back-name" x="552" y="502" text-anchor="middle">Tom Varulek</text>
</svg>

</body>
</html>
```